Stationary Set Rebrand for Brennick

We are a Canadian Distribution and Service Company that was established in 1969. Over the past 5 decades we have expanded our business and have warehouses across Canada. We specialize in adhesive tapes, adhesives, films, safety, warehouse, shipping, janitorial and packaging supplies.

We have updated our logo design and would like a new corporate branding identity that includes a new fresh Stationary Set (Business Cards, Letterhead, Letterhead MS Word, Envelope, Presentation Folders, Email Signatures, Notepad Covers, etc.)

Target Market(s)

Industrial Business Sector

Font styles to use
Sans Serif

Colors
0054AA
0677BA
7BADD7
CADEEF
E8F1F8
0094D4
00A9DD
6FCCEA
C7EBF8
E9F6FB
00AB8E
00BBA5
67D7C9
C6EFE9
E9F9F6
EB3D1F
EC4F4E
F09395
F8D3D4
FCEDEE

Requirements
Should not have
• Colors not too light, darker colours preferred

```html
<!DOCTYPE html>
<html lang="en">
<head>
<meta charset="utf-8">
<title>Brennick Business Card</title>
<link href="https://fonts.googleapis.com/css2?family=Open+Sans:wght@400;600;700;800&display=swap" rel="stylesheet">
<style>
  :root {
    --brand-red: #d81b21;
    --ink: #1e1e1e;
    --paper: #ffffff;
    --muted: #5a5a5a;
    --stage: #2a2a2a;
  }
  * { box-sizing: border-box; margin: 0; padding: 0; }
  html, body { width: 1200px; height: 900px; overflow: hidden; }
  body {
    background: var(--stage);
    font-family: "Open Sans", Arial, sans-serif;
    position: relative;
  }
  .card {
    position: absolute;
    left: 250px;
    width: 700px;
    height: 400px;
    overflow: hidden;
    box-shadow: 0 10px 30px rgba(0,0,0,.5);
  }
  .card--front { top: 30px; background: var(--paper); }
  .card--back { top: 470px; background: var(--brand-red); }

  .wordmark { position: absolute; }
  .wordmark__name {
    font-weight: 800;
    font-size: 72px;
    line-height: 1;
    letter-spacing: -1px;
  }
  .wordmark__tagline {
    font-weight: 700;
    font-size: 15px;
    margin-top: 4px;
    letter-spacing: .3px;
  }
  .card--front .wordmark { left: 60px; top: 44px; color: var(--ink); }
  .card--back .wordmark { right: 60px; top: 60px; color: var(--paper); text-align: right; }

  .contact-list {
    position: absolute;
    left: 60px;
    top: 180px;
    list-style: none;
    color: var(--muted);
    font-size: 20px;
  }
  .contact-list li { display: flex; align-items: center; gap: 10px; margin-bottom: 6px; }
  .contact-list svg { width: 20px; height: 20px; flex: none; }

  .address-band {
    position: absolute;
    left: 0; bottom: 0;
    width: 520px; height: 110px;
    background: var(--ink);
    color: var(--paper);
    font-size: 19px;
    line-height: 1.35;
    padding: 26px 0 0 60px;
  }
  .corner-block {
    position: absolute;
    right: 0; bottom: 0;
    width: 180px; height: 110px;
    background: var(--brand-red);
  }

  .person { position: absolute; right: 40px; top: 210px; text-align: right; }
  .person__name {
    color: var(--brand-red);
    font-weight: 700;
    font-size: 26px;
    text-transform: uppercase;
    letter-spacing: 1px;
  }
  .person__title { color: var(--muted); font-size: 20px; }
  .edge-bar {
    position: absolute;
    right: 0; top: 214px;
    width: 14px; height: 62px;
    background: var(--brand-red);
  }
</style>
</head>
<body>
  <section class="card card--front">
    <div class="wordmark">
      <div class="wordmark__name">Brennick</div>
      <div class="wordmark__tagline">Tape and Packaging Specialists</div>
    </div>

    <ul class="contact-list">
      <li>
        <svg viewBox="0 0 20 20" aria-hidden="true"><circle cx="10" cy="10" r="10" fill="var(--brand-red)"/><path d="M6 5.5c.6-.6 1.4-.5 1.8.1l1 1.5c.3.5.2 1-.2 1.4l-.6.5c.5 1.2 1.3 2 2.5 2.6l.5-.6c.4-.4 1-.5 1.4-.2l1.5 1c.6.4.7 1.2.1 1.8-1 1-2.6 1-4.2-.2-1.4-1-2.6-2.3-3.5-3.7C5 8.1 5 6.5 6 5.5z" fill="#fff"/></svg>
        044-555 018 342
      </li>
      <li>
        <svg viewBox="0 0 20 20" aria-hidden="true"><circle cx="10" cy="10" r="10" fill="var(--brand-red)"/><rect x="5" y="6.5" width="10" height="7" fill="#fff"/><path d="M5 6.5l5 4 5-4" stroke="var(--brand-red)" stroke-width="1.2" fill="none"/></svg>
        info@brennick.ca
      </li>
      <li>
        <svg viewBox="0 0 20 20" aria-hidden="true"><circle cx="10" cy="10" r="10" fill="var(--brand-red)"/><circle cx="10" cy="10" r="5" fill="none" stroke="#fff" stroke-width="1.3"/><ellipse cx="10" cy="10" rx="2" ry="5" fill="none" stroke="#fff" stroke-width="1.1"/><path d="M5 10h10" stroke="#fff" stroke-width="1.1"/></svg>
        www.brennick.ca
      </li>
    </ul>

    <div class="person">
      <div class="person__name">Marcus Delane</div>
      <div class="person__title">Managing Director</div>
    </div>
    <div class="edge-bar"></div>

    <div class="address-band">
      418 Harbour Road, Halifax<br>
      Nova Scotia, B3H 0A1
    </div>
    <div class="corner-block"></div>
  </section>

  <section class="card card--back">
    <div class="wordmark">
      <div class="wordmark__name">Brennick</div>
      <div class="wordmark__tagline">Tape and Packaging Specialists</div>
    </div>
  </section>
</body>
</html>
```